Park furniture company needs a new product flyer

We're a street and park furniture supply company and we have a new range of furniture that we would like to showcase to prospective customers.
Pictures, logo and copy attached.
Furniture pictures are also available with a black background.
Warranty information needs to feature on the flyer.
Recycled content information needs to feature on the flyer.

Target Market(s)

Landscape Architects

Font styles to use
Serif

Requirements
Must have
• Professional fonts and graphics.
Should not have
• comic sans or similar fonts - cheap graphics

```html
<!DOCTYPE html>
<html lang="en">
<head>
<meta charset="utf-8">
<title>Kerbline Commons – Product Flyer</title>
<link rel="stylesheet" href="https://fonts.googleapis.com/css2?family=Bebas+Neue&family=Montserrat:wght@300;400;600&family=Quicksand:wght@500;600&display=swap">
<style>
  :root {
    --ink-grey: #58585a;
    --footer-grey: #58585a;
    --brand-blue: #1a9ae0;
    --black: #0b0b0b;
    --white: #ffffff;
    --grass: #4aa02c;
    --grass-dark: #2f7a1c;
    --sky: #e6ebef;
    --wood-dark: #4a3e32;
    --wood-warm: #a4551c;
    --frame: #d8cfc2;
  }
  * { margin: 0; padding: 0; box-sizing: border-box; }
  html, body { width: 827px; height: 1200px; overflow: hidden; background: #ececec; }
  .flyer {
    position: relative; width: 827px; height: 1200px; overflow: hidden;
    background: var(--white); font-family: "Montserrat", sans-serif; color: var(--white);
  }
  .brand {
    position: absolute; top: 22px; left: 145px; width: 537px;
    color: var(--ink-grey); font-family: "Montserrat", sans-serif; font-weight: 600;
  }
  .brand-main { font-size: 104px; line-height: 1; letter-spacing: -2px; text-align: center; }
  .brand-sub { font-size: 38px; line-height: 1.1; text-align: right; margin-top: 2px; }
  .scene-photo {
    position: absolute; left: 0; top: 200px; width: 827px; height: 440px;
    background: linear-gradient(180deg, var(--white) 0%, var(--sky) 12%, #b9c3cb 24%, #6e8a5c 33%, var(--grass) 40%, var(--grass-dark) 100%);
  }
  .product-photo {
    position: absolute; left: 94px; top: 225px; width: 643px; height: 390px;
    border-radius: 6px;
    background: linear-gradient(180deg, var(--wood-dark) 0%, #6b5442 38%, var(--wood-warm) 62%, #8a5a34 82%, var(--frame) 100%);
    opacity: .92;
  }
  .band { position: absolute; left: 0; top: 0; width: 827px; height: 1200px; }
  .badge {
    position: absolute; left: 305px; top: 577px; width: 218px; height: 218px; border-radius: 50%;
    background: var(--black); border: 7px solid var(--white); box-shadow: 0 0 0 2px #cfcfcf;
    text-align: center; padding-top: 18px;
  }
  .badge-label { font-size: 17px; font-weight: 400; line-height: 20px; }
  .badge-figure { font-family: "Bebas Neue", sans-serif; font-size: 80px; line-height: .8; color: var(--brand-blue); margin-top: 2px; }
  .badge-list { font-family: "Quicksand", sans-serif; font-weight: 600; font-size: 12.5px; line-height: 16px; margin-top: 2px; }
  .headline {
    position: absolute; top: 806px; left: 22px; width: 783px; text-align: center; white-space: nowrap;
    font-family: "Bebas Neue", sans-serif; font-weight: 400; font-size: 44px; line-height: 1;
  }
  .subhead {
    position: absolute; top: 853px; left: 22px; width: 783px; text-align: center; white-space: nowrap;
    font-size: 22.5px; font-weight: 400; line-height: 1.1;
  }
  .copy {
    position: absolute; top: 896px; left: 22px; width: 783px;
    font-family: "Quicksand", sans-serif; font-weight: 500;
    font-size: 13.2px; line-height: 17px; text-align: center;
  }
  .copy p + p { margin-top: 16px; }
  .copy .justified { text-align: justify; text-align-last: center; }
  .footer {
    position: absolute; left: 0; top: 1088px; width: 827px; height: 112px; background: var(--footer-grey);
  }
  .phone-icon { position: absolute; left: 22px; top: 12px; }
  .call-label { position: absolute; left: 62px; top: 12px; font-size: 31px; font-weight: 300; line-height: 1; }
  .call-number { position: absolute; left: 62px; top: 42px; font-family: "Bebas Neue", sans-serif; font-size: 60px; line-height: 1; }
  .divider { position: absolute; left: 411px; top: 12px; height: 88px; border-left: 1.5px dashed #cfcfcf; }
  .contact { position: absolute; left: 470px; display: flex; align-items: center; gap: 10px; font-size: 20px; letter-spacing: 2.4px; font-weight: 400; }
  .contact-email { top: 14px; }
  .contact-web { top: 60px; }
  .contact svg { flex: none; }
</style>
</head>
<body>
<main class="flyer">
  <div class="scene-photo" role="img" aria-label="Lawn in the foreground with a city skyline fading into white behind"></div>
  <div class="product-photo" role="img" aria-label="Product photo: composite-batten table and bench seat with armrests on light aluminium frames"></div>

  <header class="brand">
    <div class="brand-main">KERBLINE</div>
    <div class="brand-sub">Commons</div>
  </header>

  <svg class="band" viewBox="0 0 827 1200" aria-hidden="true">
    <defs>
      <linearGradient id="blueFill" x1="0" y1="0" x2="0" y2="1">
        <stop offset="0" stop-color="#1b95dc"/>
        <stop offset="1" stop-color="#0e8fd8"/>
      </linearGradient>
    </defs>
    <polygon points="0,606 414,648 827,606 827,1088 0,1088" fill="#ffffff"/>
    <polygon points="0,620 414,662 827,620 827,1078 0,1078" fill="url(#blueFill)"/>
  </svg>

  <div class="badge">
    <div class="badge-label">FEATURING</div>
    <div class="badge-figure">98%</div>
    <div class="badge-list">
      recycled composite battens<br>
      stain and fade-resistant<br>
      colour options<br>
      unique aluminium<br>
      frame design
    </div>
  </div>

  <h1 class="headline">EUROPEAN INSPIRED WITH A UNIQUE AND ORIGINAL DESIGN</h1>
  <h2 class="subhead">THAT IS FUNCTIONAL ALL WHILE RESPECTING THE ENVIRONMENT</h2>

  <section class="copy">
    <p class="justified">Our range is designed to make life easier for people;<br>
    created using extremely durable, ultra low maintenance materials. he capped composite battens come with a 10-year commercial warranty covering staining, fading and structural performance.Site-specific for healthcare applications</p>
    <p class="justified">offering wheelchair accessibility options The Kerbline Commons range comprises of a seat with optional armrests, bench seat and table, available in both standard or DDA designs.</p>
    <p>Uniform length of 1800mm with tailored options available.Bolt down or freestanding options.</p>
  </section>

  <footer class="footer">
    <svg class="phone-icon" width="36" height="72" viewBox="0 0 36 72" aria-hidden="true">
      <rect x="2" y="2" width="32" height="68" rx="4" fill="none" stroke="#fff" stroke-width="3"/>
      <line x1="2" y1="10" x2="34" y2="10" stroke="#fff" stroke-width="2"/>
      <line x1="2" y1="60" x2="34" y2="60" stroke="#fff" stroke-width="2"/>
      <rect x="13" y="64" width="10" height="2.5" rx="1" fill="#fff"/>
    </svg>
    <div class="call-label">CALL US ON</div>
    <div class="call-number">12345 54321</div>
    <div class="divider"></div>
    <div class="contact contact-email">
      <svg width="28" height="28" viewBox="0 0 28 28" aria-hidden="true">
        <circle cx="14" cy="14" r="14" fill="#fff"/>
        <rect x="7" y="9" width="14" height="10" rx="1.5" fill="#1a7fc9"/>
        <polyline points="7.5,10 14,15 20.5,10" fill="none" stroke="#fff" stroke-width="1.4"/>
      </svg>
      <span>info@loremipsum.com</span>
    </div>
    <div class="contact contact-web">
      <svg width="28" height="28" viewBox="0 0 28 28" aria-hidden="true">
        <circle cx="14" cy="14" r="14" fill="#fff"/>
        <circle cx="14" cy="14" r="8" fill="none" stroke="#1a7fc9" stroke-width="1.6"/>
        <ellipse cx="14" cy="14" rx="3.5" ry="8" fill="none" stroke="#1a7fc9" stroke-width="1.3"/>
        <line x1="6" y1="14" x2="22" y2="14" stroke="#1a7fc9" stroke-width="1.3"/>
        <line x1="7.5" y1="10" x2="20.5" y2="10" stroke="#1a7fc9" stroke-width="1.1"/>
        <line x1="7.5" y1="18" x2="20.5" y2="18" stroke="#1a7fc9" stroke-width="1.1"/>
      </svg>
      <span>www.loremipsum.com</span>
    </div>
  </footer>
</main>
</body>
</html>
```